Every Shelf Set Neatly or ESN Organized needs a business card design. ESN Organized is a professi

We need a business card design that is clean, sharp and conveys a sense of organization. I already have a logo.

Target Market(s)

Families (specifically mothers), small business owners, parents, seniors

Industry/Entity Type

Business

Contact Information for Business Card

My website is www.esnorganized-example.com and my generic social link page is http://www.sociallink-example.com/everyshelfsetneatly. The phone number is 418-552-7094 and I want to be listed as Lorna M. Pelham, Owner

Requirements
Must have
• My logo.

```html
<!DOCTYPE html>
<html lang="en">
<head>
<meta charset="UTF-8">
<title>ESN Organized – Business Card</title>
<link href="https://fonts.googleapis.com/css2?family=Raleway:wght@400;500;600&family=Varela+Round&display=swap" rel="stylesheet">
<style>
  :root {
    --bg: #e9ecef;
    --card-blue: #2a7cc4;
    --card-blue-deep: #1f6fb8;
    --panel-light: #5fa3dc;
    --panel-mid: #4a92d3;
    --bar: #8fc2ec;
    --bar-text: #ffffff;
    --logo-bg: #eef0f3;
    --sheet-1: #d4dcea;
    --sheet-2: #b3c3e0;
    --logo-ink: #2a73bd;
    --title-ink: #2563a6;
    --white: #ffffff;
    --line: #a9d1f2;
  }
  * { margin: 0; padding: 0; box-sizing: border-box; }
  html, body { width: 1200px; height: 1072px; overflow: hidden; background: var(--bg); }
  .stage { position: relative; width: 1200px; height: 1072px; }
  .card {
    position: absolute; left: 100px; top: 250px;
    width: 1000px; height: 572px;
    background: linear-gradient(180deg, var(--card-blue) 0%, var(--card-blue-deep) 100%);
    overflow: hidden;
    box-shadow: 0 10px 30px rgba(0,0,0,0.18);
  }
  .name-panel {
    position: absolute; left: 0; top: 250px; width: 360px; height: 322px;
    background: var(--panel-light);
  }
  .name-panel::after {
    content: ""; position: absolute; right: 0; top: 60px; width: 40px; height: 262px;
    background: var(--panel-mid);
  }
  .sheets { position: absolute; left: 0; top: 0; }
  .logo-box {
    position: absolute; left: 0; top: 0; width: 300px; height: 200px;
    background: var(--logo-bg);
    display: flex; align-items: center; justify-content: center; gap: 14px;
  }
  .logo-box .mark { width: 22px; height: 22px; background: var(--logo-ink); }
  .logo-box .wordmark {
    font-family: "Raleway", sans-serif; font-weight: 400; font-size: 92px;
    color: var(--logo-ink); letter-spacing: 2px;
  }
  .person { position: absolute; left: 58px; top: 290px; }
  .person .name {
    font-family: "Varela Round", sans-serif; font-size: 36px; color: var(--white);
  }
  .person .role {
    font-family: "Varela Round", sans-serif; font-size: 30px; color: var(--title-ink); margin-top: 2px;
  }
  .headline { position: absolute; left: 420px; top: 105px; color: var(--white); font-family: "Raleway", sans-serif; }
  .headline .tagline { font-size: 32px; font-weight: 400; letter-spacing: 5px; margin-left: 40px; }
  .headline .big { font-size: 62px; font-weight: 500; letter-spacing: 22px; margin-top: 4px; }
  .contacts { position: absolute; left: 560px; top: 400px; }
  .contact {
    position: relative; display: flex; align-items: center;
    width: 420px; height: 34px; margin-bottom: 14px; margin-left: 40px;
    border-radius: 17px; background: var(--bar);
    font-family: "Varela Round", sans-serif; font-size: 24px; color: var(--bar-text);
    padding-left: 14px;
  }
  .connectors { position: absolute; left: 0; top: -20px; }
</style>
</head>
<body>
<div class="stage">
  <div class="card">
    <div class="name-panel"></div>
    <svg class="sheets" width="420" height="320" viewBox="0 0 420 320" aria-hidden="true">
      <polygon points="0,200 300,200 330,40 360,60 320,270 0,230" fill="var(--sheet-2)"/>
      <polygon points="0,200 300,200 320,20 340,30 310,240 0,215" fill="var(--sheet-1)"/>
    </svg>
    <div class="logo-box">
      <span class="mark"></span>
      <span class="wordmark">ESN</span>
    </div>
    <div class="person">
      <div class="name">Lorna M. Pelham</div>
      <div class="role">Owner</div>
    </div>
    <div class="headline">
      <div class="tagline">Every Shelf Set Neatly</div>
      <div class="big">ORGANIZED</div>
    </div>
    <div class="contacts">
      <svg class="connectors" width="60" height="170" viewBox="0 0 60 170" aria-hidden="true">
        <line x1="22" y1="36" x2="22" y2="150" stroke="var(--line)" stroke-width="3"/>
        <line x1="32" y1="80" x2="32" y2="150" stroke="var(--line)" stroke-width="3"/>
        <line x1="42" y1="126" x2="42" y2="150" stroke="var(--line)" stroke-width="3"/>
        <circle cx="22" cy="30" r="9" fill="none" stroke="var(--line)" stroke-width="3"/>
        <line x1="13" y1="30" x2="31" y2="30" stroke="var(--line)" stroke-width="2"/>
        <circle cx="32" cy="74" r="8" fill="var(--line)"/>
        <path d="M36 114 l4 0 l2 6 l-3 2 a12 12 0 0 0 6 6 l2 -3 l6 2 l0 4 a3 3 0 0 1 -3 3 a20 20 0 0 1 -17 -17 a3 3 0 0 1 3 -3z" fill="var(--line)"/>
      </svg>
      <div class="contact">www.esnorganized-example.com</div>
      <div class="contact">/everyshelfsetneatly</div>
      <div class="contact">418-552-7094</div>
    </div>
  </div>
</div>
</body>
</html>
```